Plakat-Design für Immobilienmakler und Baufinanzierer
Zielgruppe
Wir sind Immobilienmakler und Baufinanzierer und suchen ein hochwertiges Design, unsere Zielgruppe sind Kunden, die Ihr Haus verkaufen möchten. Für jeden erfolgreichen Verkauf spenden wir 5 % unserer Maklercourtage an einen Verein, den sich der Kunde aussuchen darf. Mit diesem Plakat wollen wir auf unsere Vereinsförderng aufmerksam machen und Vereine ansprechen.
Aufgabenstellung
Text: 'Wir spenden 5 % unserer Provision für Ihren Verein', 'Nur 1,99 % Maklercourtage', Logo, Kontaktdaten

```html
<!DOCTYPE html>
<html lang="de">
<head>
<meta charset="utf-8">
<title>Plakat – Vereinsförderung</title>
<link rel="stylesheet" href="https://fonts.googleapis.com/css2?family=Raleway:wght@400;500;800&display=swap">
<style>
  :root {
    --teal-deep: #1b3a3d;
    --teal-photo: #3f8c90;
    --teal-panel: #076e7e;
    --wine: #8e1a2c;
    --white: #ffffff;
    --logo-grey: #e9ecec;
  }
  * { margin: 0; padding: 0; box-sizing: border-box; }
  html, body { width: 846px; height: 1200px; overflow: hidden; background: var(--white); }
  .poster {
    position: relative;
    width: 846px;
    height: 1200px;
    font-family: "Raleway", sans-serif;
    color: var(--white);
    background: var(--teal-panel);
    overflow: hidden;
  }
  .hero-photo {
    position: absolute;
    left: 0; top: 0;
    width: 846px; height: 700px;
    background:
      radial-gradient(ellipse 60% 45% at 45% 65%, #5fa3a6 0%, rgba(95,163,166,0) 70%),
      linear-gradient(180deg, var(--teal-deep) 0%, var(--teal-deep) 28%, var(--teal-photo) 52%, #2f7276 100%);
  }
  .divider {
    position: absolute;
    left: 0; top: 700px;
    width: 846px; height: 7px;
    background: var(--white);
  }
  .brand {
    position: absolute;
    top: 92px; right: 56px;
    display: flex; align-items: center; gap: 10px;
  }
  .brand-mark { width: 14px; height: 14px; background: var(--logo-grey); }
  .brand-name {
    font-size: 21px; font-weight: 500; letter-spacing: 1.5px;
    text-transform: uppercase; color: var(--logo-grey);
  }
  .commission-badge {
    position: absolute;
    left: 588px; top: 535px;
    width: 238px; height: 238px;
    border-radius: 50%;
    background: var(--wine);
    display: flex; flex-direction: column; align-items: center; justify-content: center;
    text-align: center; line-height: 1.2;
  }
  .commission-badge .label { font-size: 35px; font-weight: 400; }
  .commission-badge .rate { font-size: 35px; font-weight: 800; }
  .headline {
    position: absolute;
    left: 73px; top: 808px;
    font-size: 62px; font-weight: 500; line-height: 73px;
    text-transform: uppercase; letter-spacing: 0.3px;
  }
  .headline strong { font-weight: 800; }
  .contact {
    position: absolute;
    left: 73px; top: 1052px;
    font-size: 23px; font-weight: 400;
    display: flex; align-items: center; gap: 14px;
  }
  .contact .sep { width: 1.5px; height: 28px; background: var(--white); }
</style>
</head>
<body>
  <main class="poster">
    <div class="hero-photo" role="img" aria-label="Foto: Modellhaus mit Schlüssel auf Geldscheinen, teal eingefärbt"></div>
    <div class="divider"></div>

    <div class="brand">
      <span class="brand-mark"></span>
      <span class="brand-name">Hollmann Immobilien</span>
    </div>

    <div class="commission-badge">
      <span class="label">Nur</span>
      <span class="rate">1,99 %</span>
      <span class="label">Provision</span>
    </div>

    <h1 class="headline">Wir spenden 5 %<br>unserer Provision<br>für <strong>Ihren Verein!</strong></h1>

    <p class="contact">
      <span>Interesse oder Fragen?</span>
      <span class="sep"></span>
      <span>Tel. +49 160 482 715 36</span>
    </p>
  </main>
</body>
</html>
```